New Business Card Design Project

I need a design for business cards, i am an electrical business called "Corvane Electrical and Communications" i need the cards to be double sided with the company logo on the back (attached) the front needs to say my company name, web site, email address, telephone number, and ABN number and electrical license number. I am open to different arrangements of the information but would like the background to be incorporating something electrical or something that looks smart. open to all additional ideas also.

The company colours are orange and grey see logo attached.

Business Name: Corvane Electrical and Communications
Website: corvaneelectricalandcomms.example.com.au
Email: brent@corvaneelectricalandcomms.example.com.au
Telephone(mobile): 0481209736
ABN: 71208349162
Lic No: 418273D

Target Market(s)

Business entities, Project Managers, Accounts, Clients

Industry/Entity Type

Electrician

Contact Information for Business Card

I need a design for business cards, i am an electrical business called "Corvane Electrical and Communications" i need the cards to be double sided with the company logo on the back (attached) the front needs to say my company name

Font styles to use
Serif
Sans Serif

Colors
f37122
5c5c5c

Requirements
Must have
• Must have the Logo on the back open to different ways of it being on the back but had in mind to keep it central but again open to other options
Nice to have
• A real modern cool background that is eye catching yet contemporary
Should not have
• No backgrounds of a light bulb or plug or anything like that

```html
<!DOCTYPE html>
<html lang="en">
<head>
<meta charset="utf-8">
<title>Corvane Electrical and Communications – Business Cards</title>
<link href="https://fonts.googleapis.com/css2?family=Open+Sans:wght@400;600;700&display=swap" rel="stylesheet">
<style>
  :root {
    --stage: #2b2b2d;
    --card-black: #050505;
    --band-white: #ffffff;
    --orange: #f7a51c;
    --brand-orange: #f37122;
    --grey-text: #5c5c5c;
    --white: #ffffff;
    --navy-deep: #1b2a3a;
    --navy-mid: #2c4458;
    --teal-soft: #3d5d6c;
  }
  * { box-sizing: border-box; margin: 0; padding: 0; }
  html, body {
    width: 1200px; height: 900px; overflow: hidden;
    background: var(--stage);
    font-family: "Open Sans", Arial, sans-serif;
  }
  .canvas { position: relative; width: 1200px; height: 900px; }

  .card {
    position: absolute;
    width: 600px; height: 343px;
    border-radius: 22px;
    overflow: hidden;
    box-shadow: 0 14px 34px rgba(0,0,0,.45);
  }

  /* Back side */
  .card-back { left: 110px; top: 80px; background: var(--card-black); }
  .card-back .brand {
    position: absolute; left: 0; right: 0; top: 88px;
    text-align: center; color: var(--orange); font-weight: 700;
  }
  .brand .brand-name { font-size: 64px; letter-spacing: 6px; line-height: 1; }
  .brand .brand-sub { font-size: 19px; letter-spacing: 1.5px; margin-top: 8px; }
  .brand-dot {
    display: inline-block; width: 18px; height: 18px; border-radius: 50%;
    background: var(--orange); vertical-align: middle; margin-right: 14px;
    position: relative; top: -8px;
  }
  .card-back .web-band {
    position: absolute; left: 0; right: 0; top: 247px; height: 50px;
    background: var(--band-white);
    display: flex; align-items: center; justify-content: center;
    font-size: 17px; color: var(--grey-text); letter-spacing: .2px;
  }
  .web-band .domain { color: var(--orange); }

  /* Front side */
  .card-front { left: 490px; top: 470px; }
  .card-front .backdrop {
    position: absolute; inset: 0;
    background:
      radial-gradient(circle at 32% 62%, var(--teal-soft) 0%, var(--navy-mid) 38%, transparent 70%),
      linear-gradient(135deg, var(--navy-mid) 0%, var(--navy-deep) 100%);
  }
  .card-front .person {
    position: absolute; right: 26px; top: 20px; text-align: right;
  }
  .person .person-name { color: var(--orange); font-size: 22px; letter-spacing: .5px; line-height: 1.1; }
  .person .person-role { color: var(--white); font-size: 11px; font-weight: 600; letter-spacing: .5px; }
  .card-front .brand {
    position: absolute; left: 0; right: 0; top: 98px; text-align: center;
    color: var(--orange); font-weight: 700;
  }
  .card-front .brand .brand-name { font-size: 52px; letter-spacing: 5px; }
  .card-front .brand .brand-sub { font-size: 15px; margin-top: 6px; }
  .card-front .brand .brand-dot { width: 14px; height: 14px; top: -7px; }
  .licence {
    position: absolute; left: 0; right: 0; top: 196px; text-align: center;
    color: var(--orange); font-size: 15px;
  }
  .abn {
    position: absolute; right: 22px; top: 188px; font-size: 11px; color: var(--white);
  }
  .abn .label { color: var(--orange); }
  .contact {
    position: absolute; left: 24px; bottom: 22px; list-style: none;
    color: var(--white); font-size: 12.5px; line-height: 1.6;
  }
  .contact li { display: flex; align-items: center; gap: 9px; }
  .contact svg { width: 12px; height: 12px; flex: none; }
</style>
</head>
<body>
<main class="canvas">

  <section class="card card-back" aria-label="Card back">
    <div class="brand">
      <div class="brand-name"><span class="brand-dot"></span>CORVANE</div>
      <div class="brand-sub">ELECTRICAL &amp; COMMUNICATIONS</div>
    </div>
    <div class="web-band">www.<span class="domain">corvaneelectricalandcomms.example</span>.com.au</div>
  </section>

  <section class="card card-front" aria-label="Card front">
    <div class="backdrop" role="img" aria-label="Dark blue abstract technology background with circular dial and circuit shapes"></div>

    <div class="person">
      <div class="person-name">MARLO PENNICK</div>
      <div class="person-role">DIRECTOR</div>
    </div>

    <div class="brand">
      <div class="brand-name"><span class="brand-dot"></span>CORVANE</div>
      <div class="brand-sub">ELECTRICAL &amp; COMMUNICATIONS</div>
    </div>

    <div class="licence">Lic No: 418273D</div>
    <div class="abn"><span class="label">ABN:</span> 71208349162</div>

    <ul class="contact">
      <li>
        <svg viewBox="0 0 12 12" aria-hidden="true"><path d="M2.5 1 4.5 3.2 3.6 4.6a6 6 0 0 0 3.8 3.8l1.4-.9L11 9.5 9.7 11C5 11 1 7 1 2.3Z" fill="var(--orange)"/></svg>
        0481 209 736
      </li>
      <li>
        <svg viewBox="0 0 12 12" aria-hidden="true"><rect x="1" y="2.5" width="10" height="7" rx="1" fill="none" stroke="var(--orange)" stroke-width="1.2"/><path d="M1.5 3 6 6.6 10.5 3" fill="none" stroke="var(--orange)" stroke-width="1.2"/></svg>
        brent@corvaneelectricalandcomms.example.com.au
      </li>
      <li>
        <svg viewBox="0 0 12 12" aria-hidden="true"><circle cx="6" cy="6" r="5" fill="none" stroke="var(--orange)" stroke-width="1.1"/><ellipse cx="6" cy="6" rx="2.2" ry="5" fill="none" stroke="var(--orange)" stroke-width="1"/><path d="M1 6h10" stroke="var(--orange)" stroke-width="1"/></svg>
        www.corvaneelectricalandcomms.example.com.au
      </li>
    </ul>
  </section>

</main>
</body>
</html>
```